Sleek wordpress site for Bramblecrest finishing works

We are a commercial job shop that serves B2B, govt & LEO and retail clients.We need a wordpress site with 6 individual pages: homepage, coating, laser engraving, laser cutting, part marking, and contact us. I have attached an outline of the desired flow and sub headings for each page. I would like to incorporate the colors of the logo through out the site to be clean and sleek enough to appeal to B2B commercial clients yet be inviting enough for retail clients.

I would like to have easy picture functionality so photographs on each page can be updated easily.

Target Market(s)

B2B industrial & Govt and Military part marking, laser engraving and coating: machine shops, aerospace companies, tool manufactures. Retail: personalized gifts, Job Shop

Coding

Coded - Design and coding required

Font styles to use
Sans Serif
Other font styles liked:
• Open to suggestion

Colors
0255a3
3176b5
eaf1f7
cfdeed
ffffff

Requirements
Must have
• Clean easy to navigate flow, separate pages as indicated on attached outline, high class feel. Great picture functionality, professional and inviting feel,
• **update: needs to be optimized for mobile, should have a gallery function. Gallery can be an additional page or embedded
Nice to have
• Social media connectivity links,
Should not have
• crappy plugins that make back-end management difficult, no blog

```html
<!DOCTYPE html>
<html lang="en">
<head>
<meta charset="utf-8">
<title>Bramblecrest Finishing Works</title>
<link href="https://fonts.googleapis.com/css2?family=Lato:wght@400;700;900&family=Roboto:wght@400;500;700&display=swap" rel="stylesheet">
<style>
:root{
  --blue:#0255a3;
  --blue-deep:#0a3f8f;
  --blue-mid:#3176b5;
  --blue-pale:#eaf1f7;
  --blue-soft:#cfdeed;
  --white:#ffffff;
  --ink:#1b1b1b;
  --text:#555a60;
  --ghost:#e6e8eb;
  --footer:#0d0d0e;
}
*{box-sizing:border-box;margin:0;padding:0}
html,body{width:1200px;height:3000px;overflow:hidden}
body{position:relative;background:var(--white);font-family:'Roboto',sans-serif;color:var(--text)}
a{color:inherit;text-decoration:none}

/* header */
.site-header{position:absolute;left:0;top:0;width:1200px;height:118px;border-top:4px solid var(--blue);background:var(--white)}
.brand{position:absolute;left:96px;top:22px;width:150px;display:flex;flex-direction:column;align-items:center}
.brand-mark{width:46px;height:46px;border-radius:50%;background:var(--blue)}
.brand-name{margin-top:8px;font:700 11px/1.1 'Lato',sans-serif;color:var(--blue-deep);letter-spacing:.5px;text-align:center;text-transform:uppercase}
.topbar{position:absolute;right:98px;top:32px;font-size:14px;color:#444;display:flex;gap:14px;align-items:center}
.topbar svg{width:12px;height:12px;fill:var(--blue);margin-right:6px;vertical-align:-1px}
.main-nav{position:absolute;right:98px;top:76px;display:flex;gap:22px;font:500 14px 'Roboto',sans-serif;color:#111}
.main-nav .active{color:var(--blue)}

/* hero */
.hero{position:absolute;left:0;top:118px;width:1200px;height:640px;overflow:hidden}
.hero-photo{position:absolute;inset:0;background:
  radial-gradient(ellipse 380px 160px at 560px 480px,rgba(255,190,90,.75),transparent 70%),
  radial-gradient(ellipse 500px 220px at 300px 460px,rgba(210,130,40,.5),transparent 70%),
  linear-gradient(180deg,#4a5058 0%,#2b2e33 45%,#3b2a1a 80%,#1c1a18 100%)}
.hero-title{position:absolute;top:180px;width:1200px;text-align:center;font:900 44px 'Lato',sans-serif;color:var(--white);letter-spacing:.5px}
.hero-sub{position:absolute;top:252px;width:1200px;text-align:center;font:700 20px/34px 'Lato',sans-serif;color:var(--white)}
.btn{display:inline-flex;align-items:center;justify-content:center;gap:8px;background:var(--blue-deep);color:var(--white);font:700 16px 'Lato',sans-serif;border-radius:26px}
.hero-btn{position:absolute;left:502px;top:350px;width:196px;height:48px}
.btn svg{width:15px;height:15px}
.hero-arrow{position:absolute;top:258px;width:20px;height:28px;stroke:var(--white);stroke-width:3;fill:none}
.hero-curve{position:absolute;left:0;top:460px;width:1200px;height:180px}

/* services */
.ghost{position:absolute;font:900 72px 'Lato',sans-serif;color:var(--ghost);white-space:nowrap;letter-spacing:1px}
.section-title{position:absolute;font:900 34px 'Lato',sans-serif;color:var(--ink)}
.services-intro{position:absolute;top:896px;width:1200px;text-align:center;font-size:13px;color:#666}
.service{position:absolute;top:956px;width:340px;text-align:center}
.service-pin{width:120px;height:140px;display:block;margin:0 auto}
.service h3{margin-top:14px;font:700 19px 'Roboto',sans-serif;color:#222}
.service p{margin-top:14px;font-size:13px;line-height:24px;color:#555}
.side-arrow{position:absolute;width:16px;height:24px;stroke:#666;stroke-width:2.5;fill:none}

/* strip */
.tiles{position:absolute;left:0;top:1306px;width:1200px;height:278px;display:flex}
.tile{position:relative;width:300px;height:278px}
.tile span{position:absolute;left:0;width:300px;text-align:center;font:700 23px 'Roboto',sans-serif;color:rgba(255,255,255,.35)}
.tile.featured span{color:var(--white);top:122px}
.tile:not(.featured) span{top:214px}

/* about */
.about-text{position:absolute;left:98px;width:544px;font-size:13px;line-height:22px;color:#555;text-align:justify}
.about-btn{position:absolute;left:98px;top:1940px;width:158px;height:46px;font-size:15px}
.video-frame{position:absolute;left:732px;top:1684px;width:402px;height:268px;border:3px solid var(--blue-deep)}
.video{position:absolute;left:698px;top:1718px;width:400px;height:266px;border:4px solid var(--white);box-shadow:0 2px 8px rgba(0,0,0,.25);background:
  radial-gradient(circle at 190px 150px,rgba(255,120,90,.9),transparent 40%),
  linear-gradient(160deg,#8a1b17 0%,#30343a 45%,#7f8790 70%,#1b4b8c 100%)}
.play{position:absolute;left:176px;top:116px;width:44px;height:32px;border-radius:8px;background:#d31f1f}
.play::after{content:"";position:absolute;left:17px;top:9px;border-left:13px solid var(--white);border-top:7px solid transparent;border-bottom:7px solid transparent}
.divider{position:absolute;left:98px;top:2084px;width:1004px;height:1px;background:#ddd}

/* clients & testimonials */
.sub-title{position:absolute;font:700 24px 'Roboto',sans-serif;color:#111}
.ghost.small{font-size:48px}
.mini-arrow{position:absolute;width:10px;height:16px;stroke:#777;stroke-width:2;fill:none}
.client{position:absolute;width:148px;height:76px;border:1px solid #ddd;display:flex;align-items:center;justify-content:center;gap:7px;font:700 13px 'Roboto',sans-serif;color:#333;box-shadow:0 1px 4px rgba(0,0,0,.08)}
.client i{width:10px;height:10px;background:#333;border-radius:50%;display:block}
.quote-box{position:absolute;left:628px;top:2220px;width:472px;height:132px;background:#d9d9d9;border:3px solid #bdbdbd;padding:22px 24px 0 28px;font-style:italic;font-size:12px;line-height:22px;color:#333}
.quote-box b{position:absolute;left:14px;top:10px;font-size:24px;font-style:normal;color:#666}
.quote-notch{position:absolute;left:674px;top:2351px;width:0;height:0;border-left:12px solid transparent;border-right:12px solid transparent;border-top:14px solid #bdbdbd}
.quote-name{position:absolute;left:706px;top:2378px;font:500 20px 'Roboto',sans-serif;color:#333}
.quote-name small{font-style:italic;font-size:13px;font-weight:400;color:#555}

/* footer */
.footer-curve{position:absolute;left:0;top:2470px;width:1200px;height:140px}
.site-footer{position:absolute;left:0;top:2600px;width:1200px;height:400px;background:var(--footer);color:var(--white)}
.f-title{position:absolute;top:18px;font:700 19px 'Roboto',sans-serif;color:var(--white)}
.f-title em{font-style:normal;font-weight:400;color:var(--blue-mid)}
.f-links{position:absolute;left:98px;top:68px;list-style:none;font-size:13px;line-height:26px}
.f-links li::before{content:"›";margin-right:14px;font-weight:700}
.f-contact{position:absolute;left:324px;font-size:13px;line-height:26px;display:flex;gap:16px}
.f-contact svg{width:16px;height:16px;fill:var(--white);flex:none;margin-top:5px}
.f-intro{position:absolute;left:632px;top:58px;width:470px;font-size:13px;line-height:24px}
.field{position:absolute;width:228px;height:44px;border:1px solid #cfcfcf;padding:14px 10px;font-size:11px;color:var(--white)}
.submit{position:absolute;left:872px;top:182px;width:228px;height:42px;background:var(--blue-deep);color:var(--white);font:700 17px 'Lato',sans-serif;display:flex;align-items:center;justify-content:center}
.f-rule{position:absolute;left:98px;top:296px;width:1004px;height:1px;background:#555}
.copyright{position:absolute;left:98px;top:340px;font-size:14px}
.follow{position:absolute;left:830px;top:334px;font:700 20px 'Roboto',sans-serif;display:flex;align-items:center;gap:8px}
.follow em{font-style:normal;font-weight:400;color:var(--blue-mid);margin-right:14px}
.follow i{width:30px;height:30px;border:2px solid var(--white);border-radius:50%;display:block}
</style>
</head>
<body>

<header class="site-header">
  <div class="brand">
    <span class="brand-mark"></span>
    <span class="brand-name">Bramblecrest finishing works</span>
  </div>
  <div class="topbar">
    <span><svg viewBox="0 0 24 24"><path d="M6.6 10.8a15 15 0 0 0 6.6 6.6l2.2-2.2c.3-.3.7-.4 1-.2 1.1.4 2.3.6 3.6.6.6 0 1 .4 1 1V20c0 .6-.4 1-1 1A17 17 0 0 1 3 4c0-.6.4-1 1-1h3.5c.6 0 1 .4 1 1 0 1.3.2 2.5.6 3.6.1.3 0 .7-.2 1z"/></svg>480.555.0192</span>
    <span>|</span>
    <span><svg viewBox="0 0 24 24"><path d="M2 5h20v14H2zM2 5l10 8 10-8"/></svg>info@bramblecrestworks.com</span>
  </div>
  <nav class="main-nav">
    <a class="active">HOME</a><a>COATING</a><a>LASER ENGRAVING</a><a>LASER CUTTING</a><a>PART MARKING</a><a>CONTACT</a>
  </nav>
</header>

<section class="hero">
  <div class="hero-photo" role="img" aria-label="Laser cutting head over a metal sheet throwing a shower of sparks"></div>
  <h1 class="hero-title">BRAMBLECREST FINISHING</h1>
  <p class="hero-sub">Duraglaze is a spray on ceramic based finish that can be applied<br>to metals, plastics, polymers and wood.</p>
  <a class="btn hero-btn">READ MORE <svg viewBox="0 0 20 20"><circle cx="10" cy="10" r="9" fill="#fff"/><path d="M8 5l5 5-5 5" stroke="#0a3f8f" stroke-width="2.5" fill="none"/></svg></a>
  <svg class="hero-arrow" style="left:48px" viewBox="0 0 20 28"><path d="M16 2L4 14l12 12"/></svg>
  <svg class="hero-arrow" style="left:1132px" viewBox="0 0 20 28"><path d="M4 2l12 12L4 26"/></svg>
  <svg class="hero-curve" viewBox="0 0 1200 180" preserveAspectRatio="none">
    <path d="M0 62 C400 170 800 150 1200 22 L1200 180 L0 180Z" fill="#0a3f8f"/>
    <path d="M0 70 C420 182 850 190 1200 102 L1200 180 L0 180Z" fill="#fff"/>
  </svg>
</section>

<div class="ghost" style="left:346px;top:808px">OUR SERVICES</div>
<h2 class="section-title" style="left:0;top:832px;width:1200px;text-align:center">OUR SERVICES</h2>
<p class="services-intro">We offer the wide range of services to help our customer's create whatever they needs</p>

<svg class="side-arrow" style="left:40px;top:1078px" viewBox="0 0 16 24"><path d="M13 2L3 12l10 10"/></svg>
<svg class="side-arrow" style="left:1144px;top:1078px" viewBox="0 0 16 24"><path d="M3 2l10 10L3 22"/></svg>

<div class="service" style="left:76px">
  <svg class="service-pin" viewBox="0 0 120 140"><path d="M60 134 L40 108 A56 56 0 1 1 80 108Z" fill="#0a3f8f"/><circle cx="60" cy="60" r="48" fill="none" stroke="#fff" stroke-width="2"/><rect x="42" y="42" width="30" height="34" rx="3" fill="none" stroke="#fff" stroke-width="3"/><path d="M52 72l22-22 4 4-22 22z" fill="#fff"/></svg>
  <h3>LASER ENGRAVING</h3>
  <p>Capabilities Statement: With our selection<br>of CO2 and fiber lasers there are very few materials<br>and substrates that we cannot mark</p>
</div>
<div class="service" style="left:430px">
  <svg class="service-pin" viewBox="0 0 120 140"><path d="M60 134 L40 108 A56 56 0 1 1 80 108Z" fill="#0a3f8f"/><circle cx="60" cy="60" r="48" fill="none" stroke="#fff" stroke-width="2"/><path d="M42 42l36 36M78 42L42 78" stroke="#fff" stroke-width="4"/><circle cx="44" cy="76" r="6" fill="none" stroke="#fff" stroke-width="3"/><circle cx="76" cy="76" r="6" fill="none" stroke="#fff" stroke-width="3"/></svg>
  <h3>LASER CUTTING</h3>
  <p>We can custom cut virtually any shape or design in<br>a variety of substrates or materials. Custom cut items<br>can be fabricated from wood, foam</p>
</div>
<div class="service" style="left:782px">
  <svg class="service-pin" viewBox="0 0 120 140"><path d="M60 134 L40 108 A56 56 0 1 1 80 108Z" fill="#0a3f8f"/><circle cx="60" cy="60" r="48" fill="none" stroke="#fff" stroke-width="2"/><path d="M60 38L46 60l14 24 14-24z" fill="none" stroke="#fff" stroke-width="3"/><circle cx="60" cy="62" r="4" fill="#fff"/><path d="M40 42h40" stroke="#fff" stroke-width="2"/></svg>
  <h3>PART MARKING</h3>
  <p>Nemo enim ipsam voluptatem quia voluptas<br>sit aspernatur aut odit aut fugit, sed quia consequu<br>tur magni dolores eos qui ratione volupta</p>
</div>

<div class="tiles">
  <div class="tile" role="img" aria-label="Laser engraving machine with sparks" style="background:linear-gradient(160deg,#2c3f78,#5a6a8a 45%,#c77a35 75%,#2a2a30)"><span>LASER ENGRAVING</span></div>
  <div class="tile featured" role="img" aria-label="Laser cutting nozzle over a steel plate" style="background:linear-gradient(180deg,#6f7c8c,#3a4656 55%,#1e2530)"><span>LASER CUTTING</span></div>
  <div class="tile" role="img" aria-label="Part marking laser with purple glow" style="background:radial-gradient(circle at 150px 150px,#b57ad6,transparent 40%),linear-gradient(180deg,#3a3c44,#1a1b20)"><span>PART MARKING</span></div>
  <div class="tile" role="img" aria-label="Technician spray coating a part" style="background:linear-gradient(160deg,#2f3440,#6a4a38 50%,#a36a4a 70%,#2a2a2e)"><span>COATINGS</span></div>
</div>

<div class="ghost" style="left:752px;top:1600px">ABOUT US</div>
<h2 class="section-title" style="left:98px;top:1666px">ABOUT BRAMBLECREST FINISHING</h2>
<p class="about-text" style="top:1742px">Nemo enim ipsam voluptatem quia voluptas sit aspernatur aut odit aut fugit, sed quia consequuntur magni dolores eos qui ratione voluptatem sequi nesciunt.</p>
<p class="about-text" style="top:1808px">Neque porro quisquam est, qui dolorem ipsum quia dolor sit amet, consectetur, adipisci velit, sed quia non numquam eius modi tempora incidunt ut labore et dolore magnam aliquam quaerat voluptatem. Ut enim ad minima veniam, quis nostrum exercitationem ullam corporis suscipit laboriosam, nisi ut aliquid commodi consequatur...</p>
<a class="btn about-btn">READ MORE <svg viewBox="0 0 20 20"><circle cx="10" cy="10" r="9" fill="#fff"/><path d="M8 5l5 5-5 5" stroke="#0a3f8f" stroke-width="2.5" fill="none"/></svg></a>
<div class="video-frame"></div>
<div class="video" role="img" aria-label="Video still of a laser cutting head marking a metal plate"><span class="play"></span></div>
<div class="divider"></div>

<div class="ghost small" style="left:0;top:2144px">OUR CLIENTS</div>
<h3 class="sub-title" style="left:98px;top:2158px">OUR CLIENTS</h3>
<svg class="mini-arrow" style="left:546px;top:2166px" viewBox="0 0 10 16"><path d="M8 2L2 8l6 6"/></svg>
<svg class="mini-arrow" style="left:570px;top:2166px" viewBox="0 0 10 16"><path d="M2 2l6 6-6 6"/></svg>
<div class="client" style="left:98px;top:2218px"><i></i>Redfield Beverages</div>
<div class="client" style="left:266px;top:2218px">Corvane Labs</div>
<div class="client" style="left:434px;top:2218px">Tallow Springs</div>
<div class="client" style="left:98px;top:2316px">Hartwell Pharma</div>
<div class="client" style="left:266px;top:2316px">Veltrix</div>
<div class="client" style="left:434px;top:2316px"><i></i>Kessler Tools</div>

<div class="ghost small" style="left:830px;top:2144px">TESTIMONIALS</div>
<h3 class="sub-title" style="left:628px;top:2158px">TESTIMONIALS</h3>
<svg class="mini-arrow" style="left:1066px;top:2166px" viewBox="0 0 10 16"><path d="M8 2L2 8l6 6"/></svg>
<svg class="mini-arrow" style="left:1090px;top:2166px" viewBox="0 0 10 16"><path d="M2 2l6 6-6 6"/></svg>
<div class="quote-box"><b>“</b>At vero eos et accusamus et iusto odio dignissimos ducimus qui blanditiis pre sentium voluptatum deleniti atque corrupti quos dolores et quas molestias excepturi sint occaecati cupiditate non provident,</div>
<div class="quote-notch"></div>
<p class="quote-name">Marta Quill, <small>Creative Manager, USA</small></p>

<svg class="footer-curve" viewBox="0 0 1200 140" preserveAspectRatio="none">
  <path d="M0 100 Q600 -40 1200 110 L1200 140 L0 140Z" fill="#0a3f8f"/>
  <path d="M0 110 Q600 -20 1200 120 L1200 140 L0 140Z" fill="#fff"/>
  <path d="M0 130 Q600 10 1200 130 L1200 140 L0 140Z" fill="#0d0d0e"/>
</svg>

<footer class="site-footer">
  <h4 class="f-title" style="left:96px">QUICK <em>LINKS</em></h4>
  <ul class="f-links">
    <li>Home</li><li>Coating</li><li>Laser Engraving</li><li>Laser Cutting</li><li>Part Marking</li><li>Gallery</li><li>Contact Us</li>
  </ul>
  <h4 class="f-title" style="left:324px">CONTACT <em>US</em></h4>
  <div class="f-contact" style="top:60px"><svg viewBox="0 0 24 24"><path d="M12 2a7 7 0 0 0-7 7c0 5 7 13 7 13s7-8 7-13a7 7 0 0 0-7-7zm0 9.5A2.5 2.5 0 1 1 12 6.5a2.5 2.5 0 0 1 0 5z"/></svg><span>1840 W Larkspur Ave #12,<br>Tempe, AZ 85281</span></div>
  <div class="f-contact" style="top:128px"><svg viewBox="0 0 24 24"><path d="M6.6 10.8a15 15 0 0 0 6.6 6.6l2.2-2.2c.3-.3.7-.4 1-.2 1.1.4 2.3.6 3.6.6.6 0 1 .4 1 1V20c0 .6-.4 1-1 1A17 17 0 0 1 3 4c0-.6.4-1 1-1h3.5c.6 0 1 .4 1 1 0 1.3.2 2.5.6 3.6.1.3 0 .7-.2 1z"/></svg><span>(+1) 480 555 0147</span></div>
  <div class="f-contact" style="top:170px;line-height:22px"><svg viewBox="0 0 24 24"><circle cx="12" cy="12" r="9" fill="none" stroke="#fff" stroke-width="3"/><path d="M12 7v5l3 2" stroke="#fff" stroke-width="2" fill="none"/></svg><span>Mon - Weds:&nbsp;&nbsp;&nbsp; 9am-5:30pm<br>&nbsp;&nbsp;Thu - Fri:&nbsp;&nbsp;&nbsp;&nbsp;&nbsp; 9am-7pm<br>Sat - Sun:&nbsp;&nbsp;&nbsp;&nbsp; 11am-3pm</span></div>
  <h4 class="f-title" style="left:632px">GET A <em>QUOTE</em></h4>
  <p class="f-intro">Bramblecrest Finishing offer the wide range of services to help our customer's create whatever they needs.</p>
  <div class="field" style="left:632px;top:124px">Name</div>
  <div class="field" style="left:872px;top:124px">Email</div>
  <div class="field" style="left:632px;top:180px">Phone No</div>
  <div class="submit">SUBMIT</div>
  <div class="f-rule"></div>
  <p class="copyright">Copyrights © 2018 Bramblecrest Finishing.&nbsp; All Rights Reserved&nbsp;&nbsp; |&nbsp;&nbsp; Privacy Policy.</p>
  <div class="follow">FOLLOW <em>US</em><i aria-label="Social link"></i><i aria-label="Social link"></i><i aria-label="Social link"></i><i aria-label="Social link"></i></div>
</footer>

</body>
</html>
```